Satchel & Sundial needs new business card design

I need a new business card design. I'm looking for out-of-the-box design which represents the freedom of being a location independent entrepreneur.
I offer coaching, retreats and trips.
I would like to see designs with and without the photo.
Colors I use are black (#000000), green (#25A796) and brown (#D7C38C)
Website satchelandsundial.example

Target Market(s)

location independent entrepreneurs, digital nomads, people looking to swap the 9 to 5 for a lifestyle business

Industry/Entity Type

Business

Contact Information for Business Card

Dorota Falkner
Your Lifestyle Business Coach, Retreat & Trip Leader
http://satchelandsundial.example
hello@satchelandsundial.example
Live a life you don't need a holiday from

Font styles to use
Serif
Sans Serif

Requirements
Must have
• One side should contain only the logo. I would also consider having the "Live a life you don't need a holiday from" on that side too (depending on how it looks)
• Please show both sides on the designs.

```html
<!DOCTYPE html>
<html lang="en">
<head>
<meta charset="utf-8">
<title>Satchel &amp; Sundial — Business Card</title>
<link rel="stylesheet" href="https://fonts.googleapis.com/css2?family=Open+Sans:wght@400;600&display=swap">
<style>
  :root {
    --backdrop: #3b3430;
    --card: #141516;
    --card-edge: #0c0c0d;
    --green: #25a796;
    --white: #f2f2f2;
    --grey: #a9abad;
    --rule: #d6d6d6;
  }
  * { box-sizing: border-box; margin: 0; padding: 0; }
  html, body {
    width: 1200px; height: 864px; overflow: hidden;
    background: var(--backdrop);
    font-family: "Open Sans", Arial, sans-serif;
  }
  .canvas { position: relative; width: 1200px; height: 864px; }

  .card {
    position: absolute;
    width: 540px; height: 309px;
    background: var(--card);
    border: 1px solid var(--card-edge);
    box-shadow: 0 10px 28px rgba(0,0,0,.45);
  }
  .card--front { left: 40px; top: 120px; }
  .card--back  { left: 620px; top: 430px; }

  .wordmark {
    position: absolute;
    display: flex; align-items: center; gap: 10px;
    color: var(--white);
    font-weight: 600;
    font-size: 27px;
    letter-spacing: .5px;
    text-transform: uppercase;
    white-space: nowrap;
  }
  .wordmark__square { width: 14px; height: 14px; background: var(--green); flex: none; }
  .card--front .wordmark { left: 150px; top: 104px; }
  .card--back .wordmark { right: 30px; top: 62px; font-size: 24px; }

  .social { position: absolute; right: 26px; top: 86px; display: flex; gap: 4px; }
  .social__tile { width: 15px; height: 15px; background: var(--green); }

  .tagline {
    position: absolute; left: 54px; top: 196px;
    color: var(--grey); font-size: 13px; letter-spacing: .2px;
  }

  .person { position: absolute; left: 32px; top: 150px; }
  .person__name { color: var(--green); font-size: 17px; font-weight: 600; line-height: 1.25; }
  .person__role { color: var(--white); font-size: 13.5px; line-height: 1.35; }

  .rule { position: absolute; left: 32px; right: 30px; top: 216px; height: 1px; background: var(--rule); }

  .contact { position: absolute; left: 32px; top: 228px; list-style: none; }
  .contact__item {
    display: flex; align-items: center; gap: 8px;
    color: var(--white); font-size: 12px; line-height: 1.75;
  }
  .contact__icon { width: 11px; height: 11px; flex: none; }
</style>
</head>
<body>
<main class="canvas">

  <section class="card card--front" aria-label="Business card, logo side">
    <div class="wordmark"><span class="wordmark__square"></span>Satchel &amp; Sundial</div>
    <div class="social" aria-label="Social profiles">
      <span class="social__tile"></span><span class="social__tile"></span><span class="social__tile"></span>
    </div>
    <p class="tagline">Live a life you don't need a holiday from</p>
  </section>

  <section class="card card--back" aria-label="Business card, contact side">
    <div class="wordmark"><span class="wordmark__square"></span>Satchel &amp; Sundial</div>
    <div class="person">
      <p class="person__name">Dorota Falkner</p>
      <p class="person__role">Your Lifestyle Business Coach</p>
      <p class="person__role">Retreat &amp; Trip Leader</p>
    </div>
    <div class="rule"></div>
    <ul class="contact">
      <li class="contact__item">
        <svg class="contact__icon" viewBox="0 0 12 12" aria-hidden="true">
          <rect x="0.5" y="2" width="11" height="8" fill="var(--green)"/>
          <path d="M0.5 2 L6 6.5 L11.5 2" fill="none" stroke="var(--card)" stroke-width="1"/>
        </svg>
        hello@satchelandsundial.example
      </li>
      <li class="contact__item">
        <svg class="contact__icon" viewBox="0 0 12 12" aria-hidden="true">
          <circle cx="6" cy="6" r="5.5" fill="var(--green)"/>
          <path d="M0.5 6 H11.5 M6 0.5 C3 3 3 9 6 11.5 M6 0.5 C9 3 9 9 6 11.5" fill="none" stroke="var(--card)" stroke-width=".9"/>
        </svg>
        www.satchelandsundial.example
      </li>
    </ul>
  </section>

</main>
</body>
</html>
```